We would like to obtain a sales orientated brochure to promote our two models of thermal imaging cameras as a response to the current Covid 19 health issues. I have provided the text, photos and detailed product specifications , in addition to a sample competitors brochure.
BROCHURE Details : 2 sided - front side to show product, its applications in business, school, hospitals, with text details - Back page to show specifications chart and contact information for Korvel Display Group. (Melbourne -Sydney-Perth-Brisbane - 1300 618 475
Brochure should be "eye-catching" and reflect the product as a high quality, must-have technology device for todays world.

```html
<!DOCTYPE html>
<html lang="en">
<head>
<meta charset="utf-8">
<title>Korvel Display Group – Thermal Scanning &amp; Facial Recognition Camera Brochure</title>
<link href="https://fonts.googleapis.com/css2?family=Montserrat:wght@400;500;600;700;800;900&display=swap" rel="stylesheet">
<style>
  :root{
    --stage:#5f5f5f;
    --paper-top:#d3e3f7;
    --paper-bottom:#bcd4f1;
    --brand-blue:#1747c9;
    --ink:#222a35;
    --white:#ffffff;
    --row-alt:#e6e8ec;
    --row:#f6f7f9;
    --footer-dark:#3a3a3c;
    --photo-a:#e9eef5;
    --photo-b:#9aa3ae;
  }
  *{margin:0;padding:0;box-sizing:border-box}
  html,body{width:1200px;height:800px;overflow:hidden}
  body{background:var(--stage);font-family:"Montserrat",sans-serif;color:var(--ink);position:relative}

  .page{position:absolute;top:129px;width:401px;height:543px;overflow:hidden;
        background:linear-gradient(180deg,var(--paper-top),var(--paper-bottom))}
  .page--front{left:194px}
  .page--back{left:606px}
  .abs{position:absolute}

  .brand{display:flex;align-items:center;gap:8px}
  .brand__mark{width:14px;height:14px;background:var(--brand-blue)}
  .brand__name{font-weight:500;color:var(--ink);font-size:13px;letter-spacing:.1px}

  /* front page */
  .front-brand{left:29px;top:17px}
  .title{left:29px;top:58px;font-weight:900;font-size:25.5px;line-height:25px;letter-spacing:-.3px;color:var(--brand-blue)}
  .title .dark{color:var(--ink)}
  .intro{left:173px;top:150px;width:205px;font-size:7.6px;line-height:9.4px}
  .intro h3{color:var(--brand-blue);font-weight:700;font-size:8.6px;line-height:8.8px;margin-bottom:1px}
  .blue-sweep{left:0;top:0}
  .product-photo{left:10px;top:156px;width:152px;height:352px;border-radius:6px;
        background:linear-gradient(160deg,var(--photo-a) 0%,#c3cad4 50%,var(--photo-b) 100%)}
  .label{font-size:7.3px;line-height:7.8px}
  .label--desk{left:87px;top:163px;color:var(--ink)}
  .label--floor{left:54px;top:514px;font-size:8.8px;line-height:9px;color:var(--brand-blue);font-weight:500}
  .label-line{left:0;top:0}
  .purpose{left:204px;top:277px;color:var(--white);font-weight:900;font-size:12px;line-height:12px;letter-spacing:-.1px}
  .benefits{left:205px;top:320px;width:187px;list-style:none;color:var(--white);font-size:6.9px;line-height:7.3px}
  .benefits li{position:relative;padding-left:10px;margin-bottom:5px}
  .benefits svg{position:absolute;left:0;top:1px;width:7px;height:7px}
  .benefits b{font-weight:700}
  .cta{left:228px;top:493px;color:var(--white);font-weight:700;font-size:9px;line-height:9.2px}
  .front-phone{left:223px;top:512px;display:flex;align-items:center;gap:6px;color:var(--white);font-weight:700;font-size:18px}
  .front-phone svg{width:16px;height:16px}

  /* back page */
  .usage-band{left:0;top:0}
  .usage-title{left:24px;top:14px;color:var(--white);font-weight:900;font-size:14.2px}
  .usage{left:24px;width:276px;display:flex;gap:8px;color:var(--white)}
  .usage__icon{flex:none;width:25px;height:25px;border-radius:50%;background:var(--white);display:flex;align-items:center;justify-content:center}
  .usage__icon svg{width:15px;height:15px}
  .usage__text{font-size:7.2px;line-height:7.9px}
  .usage__text b{display:block;font-weight:800;font-size:7.4px;line-height:7.9px}
  .usage--gates{top:41px}
  .usage--safety{top:72px;width:250px}
  .usage--legal{top:104px;width:150px}
  .back-photo{left:302px;top:14px;width:88px;height:180px;border-radius:6px;
        background:linear-gradient(160deg,#eef2f8 0%,#b9c2cd 55%,#6f7884 100%)}
  .specs-title{left:0;width:401px;top:178px;text-align:center;color:var(--brand-blue);font-weight:900;font-size:14.3px}

  .spec{width:182px;background:var(--white)}
  .spec h4{background:var(--brand-blue);color:var(--white);font-weight:700;font-size:8.2px;line-height:10px;padding-left:4px}
  .spec dl{display:grid;grid-template-columns:84px 1fr;font-size:5.7px;line-height:7.8px}
  .spec dt,.spec dd{background:var(--row);padding-left:4px}
  .spec dt{font-weight:600}
  .spec dt:nth-of-type(even),.spec dt:nth-of-type(even)+dd{background:var(--row-alt)}
  .spec--camera{left:12px;top:203px}
  .spec--processor{left:12px;top:272px}
  .spec--function{left:12px;top:310px}
  .spec--screen{left:210px;top:203px}
  .spec--interface{left:210px;top:251px}
  .spec--infrared{left:210px;top:350px}

  .back-brand{left:17px;top:494px}
  .web{left:257px;top:496px;color:var(--brand-blue);font-size:13px;font-weight:400}
  .web b{font-weight:800}
  .footer-bar{left:0;top:515px;width:401px;height:28px}
  .footer-text{left:15px;top:522px;color:var(--white);font-size:11px}
  .back-phone{left:262px;top:520px;display:flex;align-items:center;gap:3px;color:var(--white);font-weight:700;font-size:14px}
  .back-phone svg{width:11px;height:11px}
</style>
</head>
<body>

<section class="page page--front">
  <svg class="abs blue-sweep" width="401" height="543" viewBox="0 0 401 543" aria-hidden="true">
    <path d="M401 224 L401 543 L178 543 L168 480 Q150 330 230 300 Q300 255 401 224 Z" fill="var(--brand-blue)"/>
  </svg>

  <div class="abs brand front-brand"><span class="brand__mark"></span><span class="brand__name">Korvel Display Group</span></div>

  <h1 class="abs title"><span class="dark">THERMAL SCANNING</span> &amp;<br>FACIAL RECOGNITION<br>CAMERA</h1>

  <div class="abs intro">
    <h3>The temperature of your body is no longer considered private information.</h3>
    <p>That’s the stance that businesses around the world are taking as they install thermal imaging cameras for the safety of staff and visitors, often equipped with facial recognition technology, in their buildings in an attempt to cope with the COVID-19 pandemic. It’s a movement one might call the automation of temperature checks.</p>
  </div>

  <div class="abs product-photo" role="img" aria-label="Photo of the two thermal scanning cameras: a reception desk unit and a floor standing unit with screens"></div>

  <svg class="abs label-line" width="401" height="543" viewBox="0 0 401 543" aria-hidden="true" fill="none" stroke="var(--ink)" stroke-width=".6">
    <line x1="113" y1="181" x2="113" y2="205"/>
    <polyline points="28,505 28,524 46,524" stroke="var(--brand-blue)"/>
    <circle cx="46" cy="524" r="1.2" fill="var(--brand-blue)" stroke="none"/>
  </svg>
  <p class="abs label label--desk">Portable Camera for<br>a Reception Desk</p>
  <p class="abs label label--floor">Portable Floor<br>Standing Camera</p>

  <h2 class="abs purpose">THE PURPOSE OF THERMAL<br>SCANNING &amp; FACIAL<br>RECOGNITION</h2>

  <ul class="abs benefits">
    <li><svg viewBox="0 0 10 10"><circle cx="5" cy="5" r="5" fill="#fff"/><path d="M2.8 5.2 4.4 6.7 7.3 3.6" stroke="var(--brand-blue)" stroke-width="1.3" fill="none"/></svg>The purpose is to identify <b>anyone walking into an establishment with a high temperature.</b> This will reduce the likelihood of spreading any <b>potential virus and brings some peace of mind</b> to people in the building.</li>
    <li><svg viewBox="0 0 10 10"><circle cx="5" cy="5" r="5" fill="#fff"/><path d="M2.8 5.2 4.4 6.7 7.3 3.6" stroke="var(--brand-blue)" stroke-width="1.3" fill="none"/></svg>We can <b>pair your thermal camera/s</b> with facial recognition software.</li>
    <li><svg viewBox="0 0 10 10"><circle cx="5" cy="5" r="5" fill="#fff"/><path d="M2.8 5.2 4.4 6.7 7.3 3.6" stroke="var(--brand-blue)" stroke-width="1.3" fill="none"/></svg><b>Employees will check in by standing in front of the camera,</b> which identifies them by their face in just a few seconds without contact (with or without a mask on) and simultaneously performs a thermal scan.</li>
    <li><svg viewBox="0 0 10 10"><circle cx="5" cy="5" r="5" fill="#fff"/><path d="M2.8 5.2 4.4 6.7 7.3 3.6" stroke="var(--brand-blue)" stroke-width="1.3" fill="none"/></svg><b>It will record a photo of the individual, the date, the time</b> and the temperature reading at that time of entering the building.</li>
    <li><svg viewBox="0 0 10 10"><circle cx="5" cy="5" r="5" fill="#fff"/><path d="M2.8 5.2 4.4 6.7 7.3 3.6" stroke="var(--brand-blue)" stroke-width="1.3" fill="none"/></svg>If the <b>camera detects a high temperature reading,</b> it will sound an alarm in real time and send a notification to a nominated <b>administrator/in-house security.</b></li>
  </ul>

  <p class="abs cta">FOR FURTHER INFORMATION &amp;<br>A FREE QUOTE</p>
  <div class="abs front-phone">
    <svg viewBox="0 0 24 24" fill="none" stroke="#fff" stroke-width="2"><path d="M22 16.9v3a2 2 0 0 1-2.2 2 19.8 19.8 0 0 1-8.6-3.1 19.5 19.5 0 0 1-6-6A19.8 19.8 0 0 1 2.1 4.2 2 2 0 0 1 4.1 2h3a2 2 0 0 1 2 1.7c.1 1 .4 1.9.7 2.8a2 2 0 0 1-.5 2.1L8 9.9a16 16 0 0 0 6 6l1.3-1.3a2 2 0 0 1 2.1-.4c.9.3 1.8.6 2.8.7a2 2 0 0 1 1.7 2z"/></svg>
    <span>1300 618 475</span>
  </div>
</section>

<section class="page page--back">
  <svg class="abs usage-band" width="401" height="200" viewBox="0 0 401 200" aria-hidden="true">
    <path d="M0 0 L374 0 Q350 75 290 105 L140 162 Q90 178 50 168 Q15 158 0 130 Z" fill="var(--brand-blue)"/>
  </svg>

  <h2 class="abs usage-title">WHERE &amp; HOW CAN IT BE USED?</h2>

  <div class="abs usage usage--gates">
    <span class="usage__icon"><svg viewBox="0 0 24 24" fill="none" stroke="var(--brand-blue)" stroke-width="1.8"><rect x="4" y="3" width="16" height="18"/><line x1="9" y1="7" x2="9" y2="21"/><line x1="15" y1="7" x2="15" y2="21"/><line x1="4" y1="7" x2="20" y2="7"/></svg></span>
    <p class="usage__text"><b>THIS CAMERA CAN BE USED WITH ACCESS CONTROL GATES.</b>It is used in office buildings, schools, hotels, hospitality, in fact, any space where Covid is potentially a threat to staff or visitors.</p>
  </div>
  <div class="abs usage usage--safety">
    <span class="usage__icon"><svg viewBox="0 0 24 24" fill="none" stroke="var(--brand-blue)" stroke-width="1.8"><path d="M3 8V3h5M16 3h5v5M21 16v5h-5M8 21H3v-5"/><circle cx="12" cy="10" r="3"/><path d="M7 18c1-3 3-4 5-4s4 1 5 4"/></svg></span>
    <p class="usage__text"><b>OUR THERMAL SCANNING &amp; FACIAL RECOGNITION CAMERA</b>is used as a safety and security measure.</p>
  </div>
  <div class="abs usage usage--legal">
    <span class="usage__icon"><svg viewBox="0 0 24 24" fill="none" stroke="var(--brand-blue)" stroke-width="1.8"><path d="M12 2 4 5v6c0 5 3.5 9 8 11 4.5-2 8-6 8-11V5z"/><path d="M8.5 12l2.5 2.5 4.5-5"/></svg></span>
    <p class="usage__text"><b>IF SOMEONE GETS SICK AND TAKES LEGAL ACTION,</b>you can demonstrate that you have made your best effort to protect your staff and visitors.</p>
  </div>

  <div class="abs back-photo" role="img" aria-label="Photo of the desk and floor standing thermal cameras"></div>

  <h2 class="abs specs-title">TECHNICAL SPECIFICATIONS</h2>

  <div class="abs spec spec--camera">
    <h4>CAMERA</h4>
    <dl>
      <dt>Resolution:</dt><dd>2 million pixels</dd>
      <dt>Type:</dt><dd>Binocular wide dynamic camera</dd>
      <dt>Aperture:</dt><dd>F2.4</dd>
      <dt>Focusing distance:</dt><dd>50-150cm</dd>
      <dt>White balance:</dt><dd>auto</dd>
      <dt>Photo flood light:</dt><dd>LED &amp; IR dual photo flood light</dd>
    </dl>
  </div>

  <div class="abs spec spec--processor">
    <h4>PROCESSOR</h4>
    <dl>
      <dt>CPU:</dt><dd>KX3200 quad-core</dd>
      <dt>Storage:</dt><dd>EMMC 8G</dd>
    </dl>
  </div>

  <div class="abs spec spec--function">
    <h4>FUNCTION</h4>
    <dl>
      <dt>Face Detection:</dt><dd>Supports facial detection</dd>
      <dt>Face library:</dt><dd>Up to 30,000</dd>
      <dt>1: N face recognition:</dt><dd>Support</dd>
      <dt>1: 1 face comparison:</dt><dd>Support</dd>
      <dt>Stranger detection:</dt><dd>Support</dd>
      <dt>Identify distance configuration:</dt><dd>Support</dd>
      <dt>UI interface configuration:</dt><dd>Support</dd>
      <dt>Upgrade remotely:</dt><dd>Support</dd>
      <dt>Interface:</dt><dd>Interfaces include device management, personnel /photo management, record query, etc.</dd>
      <dt>Deployment method:</dt><dd>Support public cloud deployment, privatized deployment, LAN use, stand-alone use</dd>
    </dl>
  </div>

  <div class="abs spec spec--screen">
    <h4>SCREEN</h4>
    <dl>
      <dt>Size:</dt><dd>8.0 inch IPS LCD screen</dd>
      <dt>Resolution:</dt><dd>800×1280</dd>
      <dt>Touch:</dt><dd>Not supported</dd>
    </dl>
  </div>

  <div class="abs spec spec--interface">
    <h4>INTERFACE</h4>
    <dl>
      <dt>Network module:</dt><dd>Ethernet and wireless (WIFI)</dd>
      <dt>Audio:</dt><dd>2.5W / 4R speakers</dd>
      <dt>USB:</dt><dd>1 USB OTG, 1 USB HOST standard A port</dd>
      <dt>Serial communication:</dt><dd>1 RS232 serial port</dd>
      <dt>Relay output:</dt><dd>1 door open signal output</dd>
      <dt>Wiegand One Wiegand:</dt><dd>26/34 output, one Wiegand 26/34 input</dd>
      <dt>Upgrade button:</dt><dd>Support Uboot upgrade button</dd>
      <dt>Wired network:</dt><dd>1 RJ45 Ethernet socket</dd>
    </dl>
  </div>

  <div class="abs spec spec--infrared">
    <h4>INFRARED IMAGING THERMAL MODULE</h4>
    <dl>
      <dt>Temperature detection:</dt><dd>Support</dd>
      <dt>Temperature detection distance:</dt><dd>1 meter (optimal distance 0.5 meter)</dd>
      <dt>Temperature:</dt><dd>≤ ±0.5℃ measurement accuracy</dd>
      <dt>Temperature measurement range</dt><dd>10℃-42℃</dd>
      <dt>Pixels:</dt><dd>32 X 32 dots (total 1024 pixels)</dd>
      <dt>Visitors’ temperature is normal &amp;released directly:</dt><dd>Support</dd>
      <dt>Abnormal temperature alarm:</dt><dd>Support (temperature alarm value can be set)</dd>
    </dl>
  </div>

  <div class="abs brand back-brand"><span class="brand__mark"></span><span class="brand__name">Korvel Display Group</span></div>
  <p class="abs web"><b>korveldisplay</b>.com.au</p>

  <svg class="abs footer-bar" viewBox="0 0 401 28" width="401" height="28" aria-hidden="true">
    <rect width="401" height="28" fill="var(--footer-dark)"/>
    <polygon points="244,0 401,0 401,28 234,28" fill="var(--brand-blue)"/>
  </svg>
  <p class="abs footer-text">For further information &amp; a free quote</p>
  <div class="abs back-phone">
    <svg viewBox="0 0 24 24" fill="none" stroke="#fff" stroke-width="2.2"><path d="M22 16.9v3a2 2 0 0 1-2.2 2 19.8 19.8 0 0 1-8.6-3.1 19.5 19.5 0 0 1-6-6A19.8 19.8 0 0 1 2.1 4.2 2 2 0 0 1 4.1 2h3a2 2 0 0 1 2 1.7c.1 1 .4 1.9.7 2.8a2 2 0 0 1-.5 2.1L8 9.9a16 16 0 0 0 6 6l1.3-1.3a2 2 0 0 1 2.1-.4c.9.3 1.8.6 2.8.7a2 2 0 0 1 1.7 2z"/></svg>
    <span>1300 618 475</span>
  </div>
</section>

</body>
</html>
```